IT Company requires new Business Card design.

Over the years we have had a few different business card designs. We are now due for new cards across the board for all staff. We felt this would be a good time to start fresh with a new design. Our traditional card simply had our details on the front, and a list of services on the back. We don't particularly need the list of services, we have had cards where the only thing on the rear of the card was our logo.
Feel free to be creative, we would like our tag line "Complete IT Management" to appear at some point, doesn't necessarily have to be with the logo.
I have attached samples and drafts of various previous cards we have used over the years.

```html
<!DOCTYPE html>
<html lang="en">
<head>
<meta charset="utf-8">
<title>Corrin Netlink – Business Card</title>
<link rel="stylesheet" href="https://fonts.googleapis.com/css2?family=Open+Sans:wght@400;600;700&display=swap">
<style>
  :root {
    --page: #e8e8e8;
    --card: #ffffff;
    --slate: #5f6f7a;
    --slate-dark: #3f454a;
    --ink: #55626b;
    --rule: #c9cdd0;
    --on-band: #ffffff;
  }
  * { box-sizing: border-box; margin: 0; padding: 0; }
  html, body {
    width: 1034px; height: 1200px; overflow: hidden;
    background: var(--page);
    font-family: "Open Sans", Arial, sans-serif;
  }
  .card {
    position: absolute; left: 67px; width: 900px; height: 514px;
    background: var(--card);
    box-shadow: 0 3px 10px rgba(0,0,0,.18);
    overflow: hidden;
  }
  .card--front { top: 62px; }
  .card--back { top: 626px; }

  .brand { position: absolute; left: 62px; top: 150px; width: 370px; }
  .brand__name {
    display: flex; align-items: center; gap: 14px;
    color: var(--slate); font-weight: 700; font-size: 38px; line-height: 1.05;
  }
  .brand__mark { width: 40px; height: 40px; background: var(--slate); flex: none; }
  .brand__tagline {
    margin-top: 10px; margin-left: 54px;
    color: var(--slate); font-size: 12px; font-weight: 600; letter-spacing: 3px;
    text-transform: uppercase;
  }

  .divider { position: absolute; left: 460px; top: 58px; width: 2px; height: 285px; background: var(--rule); }

  .person { position: absolute; left: 486px; top: 76px; color: var(--ink); }
  .person__name { font-size: 26px; font-weight: 700; color: var(--slate); }
  .person__role { font-size: 21px; margin-top: 2px; }

  .contacts { position: absolute; left: 486px; top: 157px; list-style: none; color: var(--ink); }
  .contacts li { display: flex; align-items: center; height: 38px; font-size: 21px; }
  .contacts svg { width: 18px; height: 18px; margin-right: 12px; fill: var(--slate); flex: none; }

  .wave { position: absolute; left: 0; bottom: 0; width: 900px; height: 514px; }
  .address {
    position: absolute; right: 66px; top: 436px; text-align: right;
    color: var(--on-band); font-size: 20px; line-height: 32px;
  }

  .back-brand {
    position: absolute; left: 0; right: 0; top: 170px;
    display: flex; justify-content: center; align-items: center; gap: 26px;
    color: var(--slate); font-weight: 700; font-size: 66px;
  }
  .back-brand__mark { width: 70px; height: 70px; background: var(--slate); }
  .back-tagline {
    position: absolute; left: 0; right: 0; top: 275px; text-align: center;
    color: var(--slate); font-size: 15px; font-weight: 600; letter-spacing: 5px; text-transform: uppercase;
  }
  .back-url {
    position: absolute; left: 0; right: 0; top: 464px; text-align: center;
    color: var(--slate-dark); font-size: 24px; letter-spacing: 2px;
  }
</style>
</head>
<body>
  <section class="card card--front">
    <div class="brand">
      <div class="brand__name"><span class="brand__mark"></span>Corrin Netlink</div>
      <div class="brand__tagline">Complete IT Management</div>
    </div>

    <div class="divider"></div>

    <div class="person">
      <div class="person__name">Daniel Reeve</div>
      <div class="person__role">Operation Manager</div>
    </div>

    <ul class="contacts">
      <li><svg viewBox="0 0 24 24"><path d="M6.6 10.8a15 15 0 0 0 6.6 6.6l2.2-2.2a1 1 0 0 1 1-.25 11.4 11.4 0 0 0 3.6.6 1 1 0 0 1 1 1V20a1 1 0 0 1-1 1A17 17 0 0 1 3 4a1 1 0 0 1 1-1h3.5a1 1 0 0 1 1 1 11.4 11.4 0 0 0 .6 3.6 1 1 0 0 1-.25 1z"/></svg>08 5550 1840</li>
      <li><svg viewBox="0 0 24 24"><path d="M7 1h10a2 2 0 0 1 2 2v18a2 2 0 0 1-2 2H7a2 2 0 0 1-2-2V3a2 2 0 0 1 2-2zm0 3v13h10V4zm5 15a1 1 0 1 0 0 2 1 1 0 0 0 0-2z"/></svg>0400 555 918</li>
      <li><svg viewBox="0 0 24 24"><path d="M6 2h10l2 2v5H6zM3 10h18a2 2 0 0 1 2 2v7H1v-7a2 2 0 0 1 2-2zm3 6v5h12v-5z"/></svg>08 5550 1840</li>
      <li><svg viewBox="0 0 24 24"><path d="M2 6h20v13H2zm2 2v.4l8 5 8-5V8l-8 5z"/></svg>daniel@corrinnetlink.com.au</li>
      <li><svg viewBox="0 0 24 24"><path d="M12 2a10 10 0 1 0 0 20 10 10 0 0 0 0-20zm6.9 9h-3a15 15 0 0 0-1.2-5.6A8 8 0 0 1 18.9 11zM12 4.1c.9 1.2 1.8 3.6 1.9 6.9h-3.8c.1-3.3 1-5.7 1.9-6.9zM9.3 5.4A15 15 0 0 0 8.1 11h-3a8 8 0 0 1 4.2-5.6zM5.1 13h3a15 15 0 0 0 1.2 5.6A8 8 0 0 1 5.1 13zm6.9 6.9c-.9-1.2-1.8-3.6-1.9-6.9h3.8c-.1 3.3-1 5.7-1.9 6.9zm2.7-1.3a15 15 0 0 0 1.2-5.6h3a8 8 0 0 1-4.2 5.6z"/></svg>www.corrinnetlink.com.au</li>
    </ul>

    <svg class="wave" viewBox="0 0 900 514" aria-hidden="true">
      <path d="M0 476 C 260 500, 520 388, 900 398 L900 514 L0 514 Z" fill="var(--slate)"/>
      <path d="M0 452 C 270 498, 520 362, 900 376 L900 386 C 520 378, 270 505, 0 468 Z" fill="var(--slate-dark)"/>
      <path d="M0 470 C 262 497, 520 382, 900 392" stroke="#ffffff" stroke-width="2" fill="none"/>
    </svg>

    <address class="address" style="font-style:normal">
      Unit 4 12 Harbour Rise<br>Kelmont WA 6999
    </address>
  </section>

  <section class="card card--back">
    <div class="back-brand"><span class="back-brand__mark"></span>Corrin Netlink</div>
    <div class="back-tagline">Complete IT Management</div>
    <div class="back-url">www.corrinnetlink.com.au</div>
  </section>
</body>
</html>
```